Driver License Monitoring Application Marketing Website

We need a new web design for our web application. The product is called "RoadPermitGuard." We provide a driver license monitoring service to companies and local government bodies with driver fleets. Our current website is available at www.RoadPermitGuard-example.com.

I prefer a clean, single-page design with good SEO. Attached are some PDFs with data about the project.

Target Market(s)

Companies with driver fleets, local government.

Industry/Entity Type

Government

Coding

Coded - Design and coding required

Number of Pages Required

1 page

Colors
000000

Requirements
Must have
• Content from current www.RoadPermitGuard-example.com and attached PDFs.
Nice to have
• Prefer a simple Bootstrap or similar design for easy editing.
• Room for a simple video explanation of how the product works (we don't have an actual video yet)

```html
<!DOCTYPE html>
<html lang="en">
<head>
<meta charset="utf-8">
<title>RoadPermitGuard — Online Driver Management</title>
<link rel="stylesheet" href="https://fonts.googleapis.com/css2?family=Source+Sans+3:wght@300;400;600;700&family=Open+Sans:wght@400;600;700&display=swap">
<style>
  :root {
    --brand-red: #b3191f;
    --band-red: #ad1c22;
    --ink: #2f3238;
    --text: #333333;
    --muted: #9a9a9a;
    --field: #f5f5f5;
    --rule: #dcdcdc;
    --footer: #141518;
    --footer-bottom: #0f1012;
    --white: #ffffff;
  }
  * { box-sizing: border-box; margin: 0; padding: 0; }
  html, body { width: 805px; height: 1200px; overflow: hidden; background: var(--white); }
  body { position: relative; font-family: "Open Sans", Arial, sans-serif; color: var(--text); }

  .hero { position: absolute; left: 0; top: 0; width: 805px; height: 336px; }
  .hero-photo { position: absolute; inset: 0;
    background: linear-gradient(100deg, #5a0d10 0%, #8e1a1d 30%, #3a0a0c 60%, #1c1a1c 100%); }
  .hero-shade { position: absolute; inset: 0; background: linear-gradient(90deg, rgba(0,0,0,.15), rgba(0,0,0,.45)); }
  .hero-copy { position: absolute; left: 400px; width: 342px; top: 78px; text-align: center; color: var(--white); }
  .hero-title { font-family: "Source Sans 3", sans-serif; font-weight: 300; font-size: 31px; letter-spacing: -1px; line-height: 1; }
  .hero-lead { margin-top: 16px; font-family: "Source Sans 3", sans-serif; font-size: 12.5px; line-height: 19px; letter-spacing: 2px; text-transform: uppercase; }
  .btn-learn { position: absolute; left: 510px; top: 232px; width: 113px; height: 33px; background: var(--brand-red);
    color: var(--white); font-size: 8px; font-weight: 700; letter-spacing: 1.3px; display: flex; align-items: center; justify-content: center; }

  .section-rule { position: absolute; left: 68px; width: 669px; top: 428px; height: 1px; background: var(--rule); }
  .section-icon { position: absolute; left: 387px; top: 412px; width: 32px; height: 32px; border: 1px solid var(--rule); border-radius: 50%; background: var(--white); display: flex; align-items: center; justify-content: center; }
  .contact-title { position: absolute; left: 0; width: 805px; top: 458px; text-align: center; font-family: "Source Sans 3", sans-serif; font-weight: 700; font-size: 23px; letter-spacing: -1px; color: var(--ink); }
  .title-underline { position: absolute; left: 352px; width: 102px; top: 493px; height: 1px; background: var(--rule); }
  .title-underline::after { content: ""; position: absolute; left: 29px; top: 6px; width: 44px; height: 1px; background: var(--rule); }
  .contact-intro { position: absolute; left: 0; width: 805px; top: 523px; text-align: center; font-size: 9px; line-height: 16px; color: var(--text); }

  .contact-form { position: absolute; left: 68px; top: 581px; width: 325px; }
  .field { display: block; width: 325px; height: 28px; background: var(--field); margin-bottom: 13.5px; padding-left: 9px;
    font-size: 8.5px; color: var(--muted); line-height: 28px; }
  .field-message { height: 70px; line-height: 1; padding-top: 8px; font-family: monospace; font-size: 8px; }
  .btn-send { position: absolute; left: 0; top: 207px; width: 139px; height: 30px; border: 2px solid var(--ink);
    font-size: 7.5px; font-weight: 700; letter-spacing: .6px; display: flex; align-items: center; justify-content: center; color: var(--ink); }

  .map { position: absolute; left: 413px; top: 581px; width: 324px; height: 116px;
    background: linear-gradient(135deg, #e9e5dc 0%, #e3e6d6 55%, #9cc0e8 75%, #e9e5dc 100%); border: 2px solid #ececec; }
  .info-heading { position: absolute; left: 413px; top: 727px; font-size: 9.5px; font-weight: 700; color: var(--ink); }
  .info-list { position: absolute; left: 421px; top: 747px; font-size: 8.8px; color: var(--text); display: flex; gap: 20px; line-height: 16px; }
  .info-item { display: flex; gap: 3px; align-items: flex-start; }
  .info-item svg { margin-top: 4px; flex: none; }

  .cta-band { position: absolute; left: 0; top: 934px; width: 805px; height: 112px; background: var(--band-red); }
  .cta-text { position: absolute; left: 90px; width: 400px; top: 28px; text-align: center; color: #f4d6d6; font-family: "Source Sans 3", sans-serif; font-weight: 300; font-size: 17px; line-height: 25px; letter-spacing: 1.3px; }
  .btn-track { position: absolute; left: 524px; top: 39px; width: 148px; height: 35px; border: 2px solid var(--white); color: var(--white);
    font-size: 8px; font-weight: 700; letter-spacing: 1.4px; display: flex; align-items: center; justify-content: center; }

  .site-footer { position: absolute; left: 0; top: 1046px; width: 805px; height: 101px; background: var(--footer); }
  .footer-brand { position: absolute; left: 68px; top: 34px; color: var(--white); font-family: "Source Sans 3", sans-serif; font-weight: 700; font-size: 19px; letter-spacing: .3px; }
  .footer-tagline { position: absolute; left: 68px; top: 56px; color: #d8d8d8; font-size: 8px; }
  .social { position: absolute; left: 591px; top: 44px; display: flex; gap: 13px; }
  .social span { width: 12px; height: 12px; border-radius: 50%; background: var(--white); display: block; }
  .footer-bottom { position: absolute; left: 0; top: 1147px; width: 805px; height: 53px; background: var(--footer-bottom); }
  .copyright { position: absolute; left: 68px; top: 23px; font-size: 6.5px; color: #4a4a4a; }
  .mini-brand { position: absolute; right: 93px; top: 22px; font-size: 5px; font-weight: 700; color: #cfcfcf; }
</style>
</head>
<body>
  <header class="hero">
    <div class="hero-photo" role="img" aria-label="Photo of a row of red semi trucks parked side by side"></div>
    <div class="hero-shade"></div>
    <div class="hero-copy">
      <h1 class="hero-title">Online Driver Management</h1>
      <p class="hero-lead">With RoadPermitGuard, your organization will receive automated, time-critical email alerts as soon as a problem appears on a driver's license.</p>
    </div>
    <a class="btn-learn">LEARN MORE</a>
  </header>

  <div class="section-rule"></div>
  <div class="section-icon">
    <svg width="10" height="9" viewBox="0 0 10 9"><path d="M2 1h7l-1 7H1z" fill="#9a9ca2"/></svg>
  </div>
  <h2 class="contact-title">Contact us</h2>
  <div class="title-underline"></div>
  <p class="contact-intro">Get in touch with us in a moment. You can find our location on the map,<br>phone number to communicate with our members and email address to ask your questions. We are available.</p>

  <form class="contact-form">
    <span class="field">Name</span>
    <span class="field">Email</span>
    <span class="field">Subject</span>
    <span class="field field-message">Message</span>
    <span class="btn-send">SEND YOUR MESSAGE</span>
  </form>

  <div class="map" role="img" aria-label="Street map showing the office location with a red pin"></div>
  <h3 class="info-heading">CONTACT INFORMATIONS</h3>
  <div class="info-list">
    <div class="info-item">
      <svg width="5" height="8" viewBox="0 0 5 8"><rect x=".5" y=".5" width="4" height="7" rx=".8" fill="none" stroke="#333"/></svg>
      <span>(+00) 5550 12 345</span>
    </div>
    <div class="info-item">
      <svg width="10" height="7" viewBox="0 0 10 7"><rect x=".5" y=".5" width="9" height="6" fill="none" stroke="#333"/><path d="M.5 .5l4.5 3.5 4.5-3.5" fill="none" stroke="#333"/></svg>
      <span>hello@roadpermitguard-example.com</span>
    </div>
    <div class="info-item">
      <svg width="6" height="9" viewBox="0 0 6 9"><path d="M3 9C1 6 0 4.5 0 3a3 3 0 0 1 6 0c0 1.5-1 3-3 6z" fill="#333"/><circle cx="3" cy="3" r="1" fill="#fff"/></svg>
      <span>12 Harbor Lane, 33 410,<br>Florida</span>
    </div>
  </div>

  <section class="cta-band">
    <p class="cta-text">MONITOR YOUR DRIVERS ELECTRONICALLY,<br>TWENTY-FOUR HOURS A DAY.</p>
    <a class="btn-track">TRACK YOUR FLEET</a>
  </section>

  <footer class="site-footer">
    <div class="footer-brand">RoadPermitGuard</div>
    <p class="footer-tagline">Created by experts in Florida traffic law.</p>
    <div class="social" aria-label="Social links">
      <span></span><span></span><span></span><span></span><span></span>
    </div>
  </footer>
  <div class="footer-bottom">
    <p class="copyright">© 2015 RoadPermitGuard. All Rights Reserved.</p>
    <span class="mini-brand">RoadPermitGuard</span>
  </div>
</body>
</html>
```